Step and Repeat Backdrop for wedding reception photo booth

Would like to have a Step and Repeat Backdrop (8 foot high by 10 foot wide) that incorporates the wedding logo (attached) and the names Helen and Gavin. Background should be white, and wedding colors are burgundy and gold. Show me creativity :-) I have included some random samples.

```html
<!DOCTYPE html>
<html lang="en">
<head>
<meta charset="UTF-8">
<title>Helen &amp; Gavin – Step and Repeat Backdrop</title>
<link rel="stylesheet" href="https://fonts.googleapis.com/css2?family=Cinzel+Decorative:wght@700;900&display=swap">
<style>
  :root {
    --burgundy: #7e1425;
    --gold: #c9a244;
    --gold-light: #e6c863;
    --gold-dark: #a9822c;
    --paper: #ffffff;
    --page: #ffffff;
    --edge: #d6d6d6;
  }
  * { margin: 0; padding: 0; box-sizing: border-box; }
  html, body {
    width: 1200px;
    height: 1200px;
    overflow: hidden;
    background: var(--page);
  }
  .canvas {
    width: 1200px;
    height: 1200px;
    display: flex;
    align-items: center;
    justify-content: center;
  }
  .backdrop {
    width: 1100px;
    height: 880px;
    background: var(--paper);
    border: 1px solid var(--edge);
    display: grid;
    grid-template-columns: repeat(6, 1fr);
    grid-template-rows: repeat(6, 1fr);
    font-family: "Cinzel Decorative", serif;
  }
  .cell {
    display: flex;
    align-items: center;
    justify-content: center;
  }
  .names {
    flex-direction: column;
    color: var(--burgundy);
    font-weight: 700;
    font-size: 27px;
    line-height: 1.05;
    text-align: center;
  }
  .names .amp { font-size: 22px; }
  .monogram {
    color: var(--gold);
    font-weight: 700;
    font-size: 50px;
    letter-spacing: -2px;
  }
  .feature-banner {
    grid-column: 2 / 6;
    grid-row: 2 / 4;
    margin: 4px 0;
    background: var(--burgundy);
    display: flex;
    align-items: center;
    justify-content: center;
  }
  .feature-title {
    font-family: "Cinzel Decorative", serif;
    font-weight: 900;
    font-size: 82px;
    background: linear-gradient(180deg, var(--gold-light) 0%, var(--gold) 50%, var(--gold-dark) 100%);
    -webkit-background-clip: text;
    background-clip: text;
    color: transparent;
    white-space: nowrap;
  }
</style>
</head>
<body>
<main class="canvas">
  <section class="backdrop" aria-label="Helen and Gavin step and repeat backdrop">
    <!-- Row 1 -->
    <div class="cell monogram" style="grid-area:1/1">H&amp;G</div>
    <div class="cell names" style="grid-area:1/2"><span>Helen</span><span class="amp">&amp;</span><span>Gavin</span></div>
    <div class="cell monogram" style="grid-area:1/3">H&amp;G</div>
    <div class="cell names" style="grid-area:1/4"><span>Helen</span><span class="amp">&amp;</span><span>Gavin</span></div>
    <div class="cell monogram" style="grid-area:1/5">H&amp;G</div>
    <div class="cell names" style="grid-area:1/6"><span>Helen</span><span class="amp">&amp;</span><span>Gavin</span></div>

    <!-- Rows 2–3 -->
    <div class="cell names" style="grid-area:2/1"><span>Helen</span><span class="amp">&amp;</span><span>Gavin</span></div>
    <div class="feature-banner"><h1 class="feature-title">Helen &amp; Gavin</h1></div>
    <div class="cell monogram" style="grid-area:2/6">H&amp;G</div>
    <div class="cell monogram" style="grid-area:3/1">H&amp;G</div>
    <div class="cell names" style="grid-area:3/6"><span>Helen</span><span class="amp">&amp;</span><span>Gavin</span></div>

    <!-- Row 4 -->
    <div class="cell names" style="grid-area:4/1"><span>Helen</span><span class="amp">&amp;</span><span>Gavin</span></div>
    <div class="cell monogram" style="grid-area:4/2">H&amp;G</div>
    <div class="cell names" style="grid-area:4/3"><span>Helen</span><span class="amp">&amp;</span><span>Gavin</span></div>
    <div class="cell monogram" style="grid-area:4/4">H&amp;G</div>
    <div class="cell names" style="grid-area:4/5"><span>Helen</span><span class="amp">&amp;</span><span>Gavin</span></div>
    <div class="cell monogram" style="grid-area:4/6">H&amp;G</div>

    <!-- Row 5 -->
    <div class="cell monogram" style="grid-area:5/1">H&amp;G</div>
    <div class="cell names" style="grid-area:5/2"><span>Helen</span><span class="amp">&amp;</span><span>Gavin</span></div>
    <div class="cell monogram" style="grid-area:5/3">H&amp;G</div>
    <div class="cell names" style="grid-area:5/4"><span>Helen</span><span class="amp">&amp;</span><span>Gavin</span></div>
    <div class="cell monogram" style="grid-area:5/5">H&amp;G</div>
    <div class="cell names" style="grid-area:5/6"><span>Helen</span><span class="amp">&amp;</span><span>Gavin</span></div>

    <!-- Row 6 -->
    <div class="cell names" style="grid-area:6/1"><span>Helen</span><span class="amp">&amp;</span><span>Gavin</span></div>
    <div class="cell monogram" style="grid-area:6/2">H&amp;G</div>
    <div class="cell names" style="grid-area:6/3"><span>Helen</span><span class="amp">&amp;</span><span>Gavin</span></div>
    <div class="cell monogram" style="grid-area:6/4">H&amp;G</div>
    <div class="cell names" style="grid-area:6/5"><span>Helen</span><span class="amp">&amp;</span><span>Gavin</span></div>
    <div class="cell monogram" style="grid-area:6/6">H&amp;G</div>
  </section>
</main>
</body>
</html>
```